Powerpoint design template for LUMOTEX for new digital platform

We would like to use a PowerPoint template, we would like to create a new page, we would like to create a new digital platform LUMOTEX for schools and parents for the creation of playful communication and educational tools for children to enhance their positive development, amaze them learn in a playful way. This platform is going to be the most creative, stimulating and innovative classroom, easy to use and fast to implement. Scrapbooking, collages ... Magazine, newsletters Diplomla / awards Slideshows Facebook Calendars Organizers Greetings Games ... This powerpoint template will be used essential to We are looking for a professional design, positioning our brand in the children market with an adult hearing. so you will need to find a good deal. Primary target: nurseries & schools from 0 to 18 years old and universities (in 2nd phase) Secondary target: small & medium businesses Third target: general public, and TPE If it is a color scheme, then it is suggested that it be marketed in Europe (UK, Italy, Spain) and in a 2nd Stage USA and other countries. multiple options for front page, insidious pages (multiple styles with limited text and extended text) and final contact page We need something to read, we can not do it too much, but we can not do it. , and inside pages aligned to our logo

Target Market(s)

Target 1; Education with teacher Target 2; parents and grandparents

Industry/Entity Type

Education

Font styles to use
Other font styles liked:
• not decided. but not too fancy

Requirements
Must have
• Multi page options for front page, page insides (multiple styles with limited text and extended text) and final page contact
Nice to have
• do not have a lot of ideas. We need something to read, we can not get away from it
Should not have
• not too fancy and busy: keep clarity & simplicity while reassuring on quality

```html
<!DOCTYPE html>
<html lang="en">
<head>
<meta charset="utf-8">
<title>Project Title Here – LUMOTEX</title>
<link rel="stylesheet" href="https://fonts.googleapis.com/css2?family=Roboto:wght@400;500;700&family=Roboto+Condensed:wght@700&display=swap">
<style>
  :root {
    --lime: #d9e243;
    --lime-light: #e6ec7c;
    --lime-pale: #eef29f;
    --orange: #f7931e;
    --ink: #222222;
    --body-text: #3a3a3a;
    --subtitle: #e3111f;
    --v1: #ee1c25;
    --v2: #6d2f5b;
    --v3: #1a82e2;
    --v4: #9ec61b;
    --feature-dark: #e1e0de;
    --feature-light: #f1f0ef;
    --cell-grey: #f1efef;
    --cell-white: #ffffff;
    --logo-accent: #2eaee5;
  }
  * { box-sizing: border-box; margin: 0; padding: 0; }
  html, body { width: 1200px; height: 900px; overflow: hidden; background: #ffffff; }
  body { font-family: "Roboto", Arial, sans-serif; color: var(--ink); }

  .slide { position: relative; width: 1200px; height: 900px; overflow: hidden; background: #fff; }

  .header-band { position: absolute; left: 0; top: 0; width: 1010px; height: 112px; }
  .slide-title {
    position: absolute; left: 30px; top: 30px;
    font-family: "Roboto Condensed", "Roboto", sans-serif; font-weight: 700;
    font-size: 48px; letter-spacing: 0.5px; color: var(--ink);
  }

  .brand { position: absolute; left: 994px; top: 40px; width: 170px; }
  .brand-name { display: flex; align-items: center; gap: 8px;
    font-weight: 700; font-size: 30px; color: var(--ink); letter-spacing: 0.5px; }
  .brand-mark { width: 16px; height: 16px; background: var(--logo-accent); flex: none; }
  .brand-tagline { margin-top: 6px; margin-left: 4px; font-size: 8px; line-height: 10px; letter-spacing: 2px; color: var(--ink); }

  .subtitle { position: absolute; left: 30px; top: 173px; font-weight: 700; font-size: 27px; color: var(--subtitle); }
  .intro { position: absolute; left: 30px; top: 211px; width: 1165px;
    font-size: 20px; line-height: 33px; letter-spacing: -0.3px; color: var(--body-text); }

  .compare {
    position: absolute; left: 25px; top: 303px;
    display: grid;
    grid-template-columns: 220px 220px 219px 270px 218px;
    grid-template-rows: 118px repeat(5, 80px);
  }
  .compare > div { display: flex; align-items: center; justify-content: center; }
  .corner-label { font-weight: 500; font-size: 28px; line-height: 34px; text-align: center; background: #fff; }
  .version-head { flex-direction: column; gap: 12px; color: #fff; font-weight: 700; font-size: 19px; padding-top: 8px; }
  .version-head svg { width: 36px; height: 36px; }
  .v1 { background: var(--v1); } .v2 { background: var(--v2); }
  .v3 { background: var(--v3); } .v4 { background: var(--v4); }

  .feature-name { font-size: 21px; color: #444; letter-spacing: -0.3px; }
  .row-odd.feature-name { background: var(--feature-dark); }
  .row-even.feature-name { background: var(--feature-light); }
  .row-odd.cell { background: var(--cell-grey); }
  .row-even.cell { background: var(--cell-white); }
  .tick { width: 33px; height: 33px; }
  .tick.t1 rect { fill: var(--v1); } .tick.t2 rect { fill: var(--v2); }
  .tick.t3 rect { fill: var(--v3); } .tick.t4 rect { fill: var(--v4); }

  .footer-band { position: absolute; left: 0; top: 832px; width: 1200px; height: 68px; }
  .footer-url { position: absolute; left: 21px; top: 854px; font-size: 22px; color: var(--ink); }
  .page-number { position: absolute; left: 1078px; top: 854px; font-size: 22px; color: var(--ink); }
</style>
</head>
<body>
<main class="slide">
  <svg class="header-band" viewBox="0 0 1010 112" aria-hidden="true">
    <polygon points="990,0 1010,0 925,112 905,112" fill="var(--lime-pale)"/>
    <polygon points="955,0 995,0 915,112 880,112" fill="var(--lime-light)"/>
    <polygon points="0,0 965,0 895,112 0,112" fill="var(--lime)"/>
  </svg>
  <h1 class="slide-title">PROJECT TITLE HERE</h1>

  <div class="brand">
    <div class="brand-name"><span class="brand-mark"></span>LUMOTEX</div>
    <div class="brand-tagline">YOUR TAGLINE<br>GOES HERE</div>
  </div>

  <h2 class="subtitle">Subtitle here</h2>
  <p class="intro">Liquorice lolly drops applicake apple pie cupcake brownie bear claw&nbsp; cake gingerbread cotton candy. Bear claw croissant apple pie. Croissant cake sweet puff wafer . Liquorice lolly drops applicake apple pie cupcake brownie</p>

  <section class="compare" aria-label="Feature comparison">
    <div class="corner-label">Special<br>Feature</div>
    <div class="version-head v1">
      <svg viewBox="0 0 24 24"><rect x="2" y="3" width="20" height="14" rx="1.5" fill="#fff"/><rect x="9" y="17" width="6" height="3" fill="#fff"/><rect x="6" y="20" width="12" height="2" fill="#fff"/></svg>
      Version One</div>
    <div class="version-head v2">
      <svg viewBox="0 0 24 24"><circle cx="12" cy="12" r="9" fill="none" stroke="#fff" stroke-width="3"/><circle cx="12" cy="12" r="4" fill="none" stroke="#fff" stroke-width="2.5"/><path d="M5.5 5.5l4 4M18.5 5.5l-4 4M5.5 18.5l4-4M18.5 18.5l-4-4" stroke="#fff" stroke-width="3"/></svg>
      Version Two</div>
    <div class="version-head v3">
      <svg viewBox="0 0 24 24"><path d="M3 5h7v7c0 4-2 6-5 7l-1-2c2-1 3-2 3-4H3z M14 5h7v7c0 4-2 6-5 7l-1-2c2-1 3-2 3-4h-4z" fill="#fff"/></svg>
      Version Three</div>
    <div class="version-head v4">
      <svg viewBox="0 0 24 24"><path d="M21 3c-6 0-10 3-12 8l4 4c5-2 8-6 8-12z" fill="#fff"/><path d="M9 11l-4 0-2 3 4 1z M13 15v4l-3 2-1-4z" fill="#fff"/><path d="M6 16c-2 1-3 3-3 5 2 0 4-1 5-3z" fill="#fff"/></svg>
      Version Four</div>

    <div class="feature-name row-odd">Feature A</div>
    <div class="cell row-odd"><svg class="tick t1" viewBox="0 0 22 22"><rect width="22" height="22" rx="4"/><path d="M5.5 11l4 4 7-8" stroke="#fff" stroke-width="2.6" fill="none"/></svg></div>
    <div class="cell row-odd"><svg class="tick t2" viewBox="0 0 22 22"><rect width="22" height="22" rx="4"/><path d="M5.5 11l4 4 7-8" stroke="#fff" stroke-width="2.6" fill="none"/></svg></div>
    <div class="cell row-odd"><svg class="tick t3" viewBox="0 0 22 22"><rect width="22" height="22" rx="4"/><path d="M5.5 11l4 4 7-8" stroke="#fff" stroke-width="2.6" fill="none"/></svg></div>
    <div class="cell row-odd"><svg class="tick t4" viewBox="0 0 22 22"><rect width="22" height="22" rx="4"/><path d="M5.5 11l4 4 7-8" stroke="#fff" stroke-width="2.6" fill="none"/></svg></div>

    <div class="feature-name row-even">Feature B</div>
    <div class="cell row-even"><svg class="tick t1" viewBox="0 0 22 22"><rect width="22" height="22" rx="4"/><path d="M5.5 11l4 4 7-8" stroke="#fff" stroke-width="2.6" fill="none"/></svg></div>
    <div class="cell row-even"><svg class="tick t2" viewBox="0 0 22 22"><rect width="22" height="22" rx="4"/><path d="M5.5 11l4 4 7-8" stroke="#fff" stroke-width="2.6" fill="none"/></svg></div>
    <div class="cell row-even"><svg class="tick t3" viewBox="0 0 22 22"><rect width="22" height="22" rx="4"/><path d="M5.5 11l4 4 7-8" stroke="#fff" stroke-width="2.6" fill="none"/></svg></div>
    <div class="cell row-even"><svg class="tick t4" viewBox="0 0 22 22"><rect width="22" height="22" rx="4"/><path d="M5.5 11l4 4 7-8" stroke="#fff" stroke-width="2.6" fill="none"/></svg></div>

    <div class="feature-name row-odd">Feature C</div>
    <div class="cell row-odd"></div>
    <div class="cell row-odd"><svg class="tick t2" viewBox="0 0 22 22"><rect width="22" height="22" rx="4"/><path d="M5.5 11l4 4 7-8" stroke="#fff" stroke-width="2.6" fill="none"/></svg></div>
    <div class="cell row-odd"><svg class="tick t3" viewBox="0 0 22 22"><rect width="22" height="22" rx="4"/><path d="M5.5 11l4 4 7-8" stroke="#fff" stroke-width="2.6" fill="none"/></svg></div>
    <div class="cell row-odd"><svg class="tick t4" viewBox="0 0 22 22"><rect width="22" height="22" rx="4"/><path d="M5.5 11l4 4 7-8" stroke="#fff" stroke-width="2.6" fill="none"/></svg></div>

    <div class="feature-name row-even">Feature D</div>
    <div class="cell row-even"></div>
    <div class="cell row-even"></div>
    <div class="cell row-even"><svg class="tick t3" viewBox="0 0 22 22"><rect width="22" height="22" rx="4"/><path d="M5.5 11l4 4 7-8" stroke="#fff" stroke-width="2.6" fill="none"/></svg></div>
    <div class="cell row-even"><svg class="tick t4" viewBox="0 0 22 22"><rect width="22" height="22" rx="4"/><path d="M5.5 11l4 4 7-8" stroke="#fff" stroke-width="2.6" fill="none"/></svg></div>

    <div class="feature-name row-odd">Feature E</div>
    <div class="cell row-odd"></div>
    <div class="cell row-odd"></div>
    <div class="cell row-odd"></div>
    <div class="cell row-odd"><svg class="tick t4" viewBox="0 0 22 22"><rect width="22" height="22" rx="4"/><path d="M5.5 11l4 4 7-8" stroke="#fff" stroke-width="2.6" fill="none"/></svg></div>
  </section>

  <svg class="footer-band" viewBox="0 0 1200 68" aria-hidden="true">
    <rect x="0" y="0" width="1200" height="68" fill="var(--lime)"/>
    <polygon points="975,0 1000,0 1050,68 1020,68" fill="var(--lime-pale)"/>
    <polygon points="995,0 1200,0 1200,68 1045,68" fill="var(--orange)"/>
  </svg>
  <div class="footer-url">www.lumotex.com</div>
  <div class="page-number">Page : 01</div>
</main>
</body>
</html>
```